Verdant Systems Business Card

want the back of card to be blue- with the logo in the center
front of card- info plus logo (info being mailing address, email address, and website address )
4 different names with titles to have on cards
1) Calvin Borsted - Owner
2) Naomi Trelvik- Customer Relationship Specialist
3) Felix Andrade- Vice President of Sales
4) Owen Markby- Chief Technology Officer

Target Market(s)

tech company in the government/probation office industry

Industry/Entity Type

Government Office

Contact Information for Business Card

1) Calvin Borsted - Owner

Colors
0355a3
ffffff

Requirements
Must have
• back side should be blue, with the logo placed in the center
• front side needs to include both the logo, as well as company info (info should include website address, email address, and mailing address)

```html
<!DOCTYPE html>
<html lang="en">
<head>
<meta charset="utf-8">
<title>Verdant Systems Business Card</title>
<link href="https://fonts.googleapis.com/css2?family=Noto+Serif:wght@600&family=Roboto:wght@400&display=swap" rel="stylesheet">
<style>
  :root {
    --backdrop: #dedede;
    --navy: #26375f;
    --navy-text: #2b3c68;
    --white: #ffffff;
    --paper: #fbfbfb;
    --grey-text: #7b7b85;
    --grey-band: #8e8e9a;
  }
  * { margin: 0; padding: 0; box-sizing: border-box; }
  html, body { width: 1200px; height: 1200px; overflow: hidden; }
  body { background: var(--backdrop); position: relative; font-family: "Roboto", Arial, sans-serif; }

  .card { position: absolute; width: 712px; height: 419px; border-radius: 22px; overflow: hidden; }

  .card-back { left: 238px; top: 118px; background: var(--navy); display: flex; align-items: center; justify-content: center; }
  .card-back .wordmark { font-family: "Noto Serif", Georgia, serif; font-weight: 600; font-size: 54px; letter-spacing: 3px; color: var(--white); text-transform: uppercase; }

  .card-front { left: 232px; top: 645px; background: var(--paper); }
  .front-logo { position: absolute; left: 28px; top: 0; width: 300px; height: 397px; display: flex; flex-direction: column; align-items: center; justify-content: center; gap: 18px; }
  .front-logo .mark-square { width: 34px; height: 34px; background: var(--navy-text); }
  .front-logo .wordmark { font-family: "Noto Serif", Georgia, serif; font-weight: 600; font-size: 25px; letter-spacing: 1px; color: var(--navy-text); text-transform: uppercase; white-space: nowrap; }

  .details { position: absolute; left: 367px; top: 95px; color: var(--grey-text); font-size: 17px; }
  .details .name { font-family: "Noto Serif", Georgia, serif; font-weight: 600; font-size: 22px; color: var(--navy-text); text-transform: uppercase; letter-spacing: 0.5px; }
  .details .title { margin-top: 6px; }
  .details .address { margin-top: 22px; line-height: 29px; }
  .contact-list { list-style: none; margin-top: 8px; }
  .contact-list li { display: flex; align-items: center; gap: 14px; height: 26px; }
  .contact-list svg { width: 16px; height: 16px; fill: var(--navy-text); flex: none; }

  .band { position: absolute; bottom: 0; height: 22px; }
  .band-navy { left: 0; width: 355px; background: var(--navy); }
  .band-grey { left: 355px; right: 0; background: var(--grey-band); }
</style>
</head>
<body>
  <section class="card card-back">
    <div class="wordmark">Verdant Systems</div>
  </section>

  <section class="card card-front">
    <div class="front-logo">
      <div class="mark-square"></div>
      <div class="wordmark">Verdant Systems</div>
    </div>

    <div class="details">
      <p class="name">Naomi Trelvik</p>
      <p class="title">Customer Relationship Specialist</p>
      <p class="address">234 Anywhere St., Any City,<br>Any Town, US 123456</p>
      <ul class="contact-list">
        <li>
          <svg viewBox="0 0 16 16" aria-hidden="true"><path d="M1 5c0-2 3-3 7-3s7 1 7 3v1h-3.5V4.5h-7V6H1z"/><path d="M3 8l2-2h6l2 2v6H3z"/></svg>
          111-111-1111
        </li>
        <li>
          <svg viewBox="0 0 16 16" aria-hidden="true"><path d="M1 3h14v1.5L8 9 1 4.5z"/><path d="M1 6.3l7 4.5 7-4.5V13H1z"/></svg>
          naomi.t@verdantsystems.com
        </li>
        <li>
          <svg viewBox="0 0 16 16" aria-hidden="true"><circle cx="8" cy="8" r="7"/><path d="M1 8h14M8 1c-3 3-3 11 0 14M8 1c3 3 3 11 0 14" stroke="#fbfbfb" stroke-width="1.1" fill="none"/></svg>
          www.verdantsystems.com
        </li>
      </ul>
    </div>

    <div class="band band-navy"></div>
    <div class="band band-grey"></div>
  </section>
</body>
</html>
```